BOLD PINE HEATING AND COOLING

Industry/Entity Type

Hvac

Requirements
Must have
• logo
My name: Gavin Pruszynski
Phone number 555-309-4461
Text:
Furnace and AC repairs
New furnace and AC installation
Ductwork
Gas lines
Water Tanks
Tankless water heaters
Nice to have
• Profesional modern look

```html
<!DOCTYPE html>
<html lang="en">
<head>
<meta charset="utf-8">
<title>Bold Pine Heating and Cooling – Business Card</title>
<link rel="stylesheet" href="https://fonts.googleapis.com/css2?family=Montserrat:wght@400;500;600;700&display=swap">
<style>
  :root {
    --bg: #e4e4e4;
    --blue: #0b6db3;
    --brand-blue: #1b4f9c;
    --red: #cf2027;
    --green: #77b843;
    --paper: #f4f4f4;
    --grey: #6d6e70;
    --white: #ffffff;
  }
  * { margin: 0; padding: 0; box-sizing: border-box; }
  html, body { width: 1200px; height: 960px; overflow: hidden; }
  body {
    background: var(--bg);
    font-family: "Montserrat", Arial, sans-serif;
    position: relative;
  }
  .card {
    position: absolute;
    left: 312px;
    width: 578px;
    height: 331px;
    background: var(--paper);
    overflow: hidden;
  }
  .card-front { top: 124px; }
  .card-back { top: 505px; }
  .card-shapes { position: absolute; inset: 0; }

  /* front */
  .brand-mark {
    position: absolute;
    left: 50%;
    transform: translateX(-50%);
    border-radius: 50%;
    background: var(--brand-blue);
  }
  .front-mark { top: 52px; width: 84px; height: 84px; }
  .brand-name {
    position: absolute;
    left: 0; right: 0;
    text-align: center;
    color: var(--brand-blue);
    font-weight: 700;
    line-height: 1;
    text-transform: uppercase;
  }
  .front-name { top: 170px; font-size: 38px; letter-spacing: 1px; }
  .front-sub { top: 212px; font-size: 15px; letter-spacing: 0.5px; }
  .web-pill {
    position: absolute;
    top: 243px;
    left: 183px;
    width: 210px;
    height: 28px;
    border-radius: 7px;
    background: var(--green);
    color: var(--white);
    font-size: 15px;
    font-weight: 500;
    text-align: center;
    line-height: 28px;
  }
  .tagline {
    position: absolute;
    top: 287px;
    left: 0; right: 0;
    text-align: center;
    color: var(--white);
    font-size: 19px;
    font-weight: 700;
  }

  /* back */
  .back-mark { top: 92px; left: 131px; transform: none; width: 64px; height: 64px; }
  .back-name { top: 184px; left: 24px; right: auto; width: 260px; font-size: 27px; }
  .back-sub { top: 214px; left: 24px; right: auto; width: 260px; font-size: 12px; }
  .person {
    position: absolute;
    top: 43px;
    right: 34px;
    color: var(--green);
    font-size: 19px;
    font-weight: 700;
    text-transform: uppercase;
  }
  .contact {
    position: absolute;
    top: 90px;
    right: 32px;
    list-style: none;
    text-align: right;
    color: var(--white);
    font-size: 14px;
    line-height: 20px;
  }
  .contact li { display: flex; align-items: center; justify-content: flex-end; gap: 3px; }
  .contact svg { width: 13px; height: 13px; }
  .services {
    position: absolute;
    top: 189px;
    right: 34px;
    list-style: none;
    text-align: right;
    color: var(--white);
    font-size: 14px;
    line-height: 19.2px;
  }
</style>
</head>
<body>

  <section class="card card-front" aria-label="Card front">
    <svg class="card-shapes" viewBox="0 0 578 331" preserveAspectRatio="none" aria-hidden="true">
      <path d="M0 0 H578 V127 Q289 104 0 127 Z" fill="var(--blue)"/>
      <path d="M0 276 Q289 254 578 276 V331 H0 Z" fill="var(--red)"/>
    </svg>
    <span class="brand-mark front-mark" aria-hidden="true"></span>
    <p class="brand-name front-name">Bold Pine</p>
    <p class="brand-name front-sub">Heating and Cooling</p>
    <p class="web-pill">www.Bold-Pine.ca</p>
    <p class="tagline">An Expert HVAC Contractor</p>
  </section>

  <section class="card card-back" aria-label="Card back">
    <svg class="card-shapes" viewBox="0 0 578 331" preserveAspectRatio="none" aria-hidden="true">
      <rect x="0" y="0" width="14" height="331" fill="var(--red)"/>
      <path d="M228 0 H578 V162 H340 Q326 162 320 150 Z" fill="var(--blue)"/>
      <path d="M340 170 H578 V331 H228 L320 182 Q326 170 340 170 Z" fill="var(--green)"/>
    </svg>
    <span class="brand-mark back-mark" aria-hidden="true"></span>
    <p class="brand-name back-name">Bold Pine</p>
    <p class="brand-name back-sub">Heating and Cooling</p>

    <p class="person">Gavin Pruszynski</p>
    <ul class="contact">
      <li>555-309-4461
        <svg viewBox="0 0 24 24" aria-hidden="true"><path fill="#fff" d="M6.6 10.8a15.1 15.1 0 0 0 6.6 6.6l2.2-2.2a1 1 0 0 1 1-.25 11.4 11.4 0 0 0 3.6.57 1 1 0 0 1 1 1V20a1 1 0 0 1-1 1A17 17 0 0 1 3 4a1 1 0 0 1 1-1h3.5a1 1 0 0 1 1 1c0 1.25.2 2.45.57 3.57a1 1 0 0 1-.25 1z"/></svg>
      </li>
      <li>www.bold-pine.ca
        <svg viewBox="0 0 24 24" aria-hidden="true"><g fill="none" stroke="#fff" stroke-width="2"><circle cx="12" cy="12" r="9"/><ellipse cx="12" cy="12" rx="4" ry="9"/><path d="M3 12h18M5 7h14M5 17h14"/></g></svg>
      </li>
    </ul>

    <ul class="services">
      <li>Furnace &amp; AC Repairs</li>
      <li>New Furnace &amp; AC Installation</li>
      <li>Ductwork</li>
      <li>Gas Lines</li>
      <li>Water Tanks</li>
      <li>Tankless Water Heaters</li>
    </ul>
  </section>

</body>
</html>
```